A website where experts collaborate on your project

I am building a new website where experts (yes, like designers) collaborate on projects with the project owner. More minds = more collaboration = better end product. Please see Pelmora(dot)com for a quick landing page I created for collaborating on presentations (although there will be many project types offered)

I am looking for a DESIGNER LONG TERM, but for now, just need initial mock ups to show the web programmers.

I have 21 Word documents loosely designed, what I would like to see here is a theme. Please DO NOT GO OFF WHAT YOU CURRENTLY SEE AT PELMORA. What is up now is only a quick landing page.

You can view a Word doc of the homepage here:
https://www.filevanta.com/s/qx83kdm2/home.docx?dl=0

WHAT AM I LOOKING FOR?
A clean, well designed theme.

Here is a link to the logo:
https://www.filevanta.com/s/mr47tpz9/logo%20-%20horizontal.tif?dl=0
-----------------------------------------
Here are a few sites I like the design of and what I like about them:
www.quenbrook.com-all around my favorite, beautiful graphics, clean layout, bold use of colors on a dark background
Ravelto.com- clean layout, The use of humans and bubble style elements.
Mintharbor.com :) clean, bold, unique pop art style but professional
plumevault.com - From the unique colors and artwork and the ability of that art to not interfere with the important elements of the site
sparkwidgets.com-clean, nice colors, well organized and separated sections.
www.dunmereco.com-love the font, use of colors and sectionalized style

All in all, I am not picky and open to so many styles. I would ultimately like the designer I pick to design all 21 pages.
Updates

Hello everyone,Moving forward, I would like you all to pay special attention to the section in my brief titled "Here are a few sites I like the design of and what I like about them". Please see below, I handpicked each one of these as sites I really like. Thank you.Here are a few sites I like the design of and what I like about them:Ravelto.com- clean layout, The use of humans and bubble style elements.Mintharbor.com :) clean, bold, unique pop art style but professionalwriteraccess.com - From the unique colors and artwork and the ability of that art to not interfere with the important elements of the sitegrowthgeeks.com-clean, nice colors, well organized and separated sections.www.dunmereco.com-love the font, use of colors and sectionalized stylewww.quenbrook.com-beautiful graphics, clean layout, bold use of colors----------------------------------------- Added Tuesday, November 24, 2015

I updated the homepage, you can see it here:https://www.dropbox.com/s/kwlkbsookq3cg2m/1new%20homepage.docx?dl=0I am modeling it after my favorite designed site: triplelift.comI love the dark colors with the orange glowing style boldness of the buttons. It's real clean too. Added Tuesday, November 24, 2015

Target Market(s)

small business owners, marketers, freelancer writers, graphic designers,

Industry/Entity Type

Building

Number of Pages Required

5+ page

Requirements
Must have
• I can't think of anything the project must have.
Nice to have
• WHAT AM I LOOKING FOR?
• A clean, well designed theme. I had a designer do a bit of work putting elements together, I found it to be very plain, but I like the Application Page (https://www.filevanta.com/s/jb19ckr3/Pelmora-Website.ai?dl=0)
• Here is a link to the logo:
• https://www.filevanta.com/s/mr47tpz9/logo%20-%20horizontal.tif?dl=0
• Here are a few sites I like the design of and what I like about them:
• Ravelto.com- clean layout, The use of humans and bubble style elements.
• Mintharbor.com :) clean, bold, unique pop art style but professional
• plumevault.com - From the unique colors and artwork and the ability of that art to not interfere with the important elements of the site
• sparkwidgets.com-clean, nice colors, well organized and separated sections.
• www.dunmereco.com-love the font, use of colors and sectionalized style
• www.quenbrook.com-beautiful graphics, clean layout, bold use of colors
• -----------------------------------------
Should not have
• out of the boxed, templated style website. I want this site to be memorable and not look like a thousand others

```html
<!DOCTYPE html>
<html lang="en">
<head>
<meta charset="utf-8">
<title>Pelmora — Experts collaborating on your project</title>
<link href="https://fonts.googleapis.com/css2?family=Open+Sans:wght@300;400;600;700&display=swap" rel="stylesheet">
<style>
:root{
  --orange:#f0901e;
  --orange-dark:#d97a0c;
  --teal:#3a9fc4;
  --ink:#555;
  --muted:#777;
  --line:#e3e3e3;
  --nav:#3b3b3b;
  --footer:#2b2b2b;
  --white:#fff;
}
*{margin:0;padding:0;box-sizing:border-box}
html,body{width:801px;height:1200px;overflow:hidden;background:var(--white)}
body{font-family:"Open Sans",Arial,sans-serif;color:var(--ink);position:relative}
.topline{position:absolute;top:0;left:0;width:801px;height:2px;background:var(--teal)}
.brand{position:absolute;left:66px;top:26px;display:flex;align-items:center;gap:8px}
.brand-name{font-size:19px;font-weight:700;color:var(--orange);letter-spacing:.3px}
.brand-dot{width:28px;height:28px;border-radius:50%;background:var(--orange)}
.notice{position:absolute;left:390px;top:18px;width:258px;height:39px;border:1px solid #d6d6d6;background:#f4f4f4;font-size:7.4px;line-height:14px;color:#666;padding:4px 10px}
.notice::after{content:"";position:absolute;right:-7px;top:15px;border-left:7px solid #d6d6d6;border-top:5px solid transparent;border-bottom:5px solid transparent}
.notify{position:absolute;left:662px;top:31px;font-size:9.5px;color:var(--teal);display:flex;align-items:center;gap:8px}
.nav{position:absolute;top:74px;left:0;width:801px;height:34px;background:var(--nav)}
.nav a{position:absolute;top:0;height:34px;line-height:34px;font-size:8.5px;color:#eee;text-decoration:none;text-align:center}
.nav .browse{left:66px;width:94px;background:var(--orange)}
.nav .sep{position:absolute;top:0;width:1px;height:34px;background:#2c2c2c}
.hero{position:absolute;top:108px;left:0;width:801px;height:370px;background:linear-gradient(90deg,#c9ccce 0%,#b9bcbf 35%,#8e9297 60%,#4c535c 80%,#a7abae 100%)}
.hero h1{position:absolute;left:66px;top:98px;font-size:47px;line-height:56px;color:var(--white);font-weight:700;letter-spacing:1px}
.hero h1 span{display:block;font-weight:400}
.hero p{position:absolute;left:67px;top:221px;font-size:12.5px;color:var(--white);font-weight:300}
.cta{position:absolute;left:67px;top:258px;width:109px;height:33px;background:linear-gradient(#f39a2b,var(--orange-dark));border-radius:3px;color:var(--white);font-size:10.5px;font-weight:700;text-align:center;line-height:33px;box-shadow:0 2px 3px rgba(0,0,0,.3)}
.arrow{position:absolute;top:164px;width:22px;height:22px;border-radius:50%;background:rgba(255,255,255,.25)}
.panel{position:absolute;top:497px;border:1px solid var(--line);border-bottom:2px solid #ddd;background:var(--white)}
.filters{left:67px;width:191px;height:404px}
.panel-head{height:32px;border-bottom:1px solid var(--line);display:flex;align-items:center;justify-content:space-between;padding:0 8px}
.filters .panel-head h2{font-size:10.5px;font-weight:600;color:var(--teal);letter-spacing:.5px}
.price{padding:8px 14px 6px;border-bottom:1px solid var(--line);height:115px}
.price h3{font-size:10px;color:var(--orange);font-weight:600;margin-bottom:3px}
.price li{list-style:none;font-size:7px;color:#666;line-height:17px}
.tick{display:inline-block;width:6px;height:6px;border:1px solid var(--teal);vertical-align:middle;margin:0 2px;position:relative;top:-1px}
.filter{height:32px;border-bottom:1px solid var(--line);display:flex;align-items:center;padding-left:14px;font-size:8.8px;color:#555;gap:10px}
.filter svg{width:10px;height:10px}
.filter:last-child{border-bottom:0}
.projects{left:274px;width:461px;height:404px}
.projects .panel-head{padding:0 10px}
.projects h2{font-size:9px;font-weight:400;color:#333;text-decoration:underline}
.sort{font-size:8px;color:var(--teal)}
.item{border-bottom:1px solid var(--line);padding:9px 10px 0;font-size:7.3px;line-height:16px;color:#666;position:relative}
.item .meta{color:var(--orange)}
.item .check{position:absolute;right:12px;top:21px}
.testimonials{position:absolute;top:920px;left:0;width:801px;text-align:center}
.testimonials h2{font-size:12.5px;color:var(--orange);font-weight:400;letter-spacing:.5px}
.testimonials p.lead{font-size:8px;line-height:17.5px;color:#666;width:590px;margin:8px auto 0}
.divider{position:absolute;top:1001px;left:226px;width:340px;height:1px;background:var(--line)}
.divider::after{content:"";position:absolute;left:166px;top:-2px;width:5px;height:5px;border-radius:50%;border:1px solid #ccc;background:var(--white)}
.avatar{position:absolute;top:1029px;width:73px;height:73px;border-radius:50%}
.quote{position:absolute;top:1037px;width:170px;font-size:7.2px;line-height:14.5px;color:#555}
.quote h4{font-size:7.8px;color:var(--teal);font-weight:400;line-height:12px}
.quote .date{margin-bottom:2px}
.chev{position:absolute;top:1062px;font-size:14px;color:#bbb;font-weight:300}
.footer{position:absolute;top:1142px;left:0;width:801px;height:58px;background:var(--footer);color:#eee}
.footer nav{position:absolute;left:67px;top:11px;font-size:7.3px}
.footer nav span{margin:0 8px;color:#bbb}
.footer small{position:absolute;left:67px;top:32px;font-size:7.2px}
.social{position:absolute;left:648px;top:21px;display:flex;gap:5px}
.social i{width:18px;height:18px;border-radius:50%;background:#555}
</style>
</head>
<body>
<div class="topline"></div>

<header>
  <div class="brand"><span class="brand-name">pelmora</span><span class="brand-dot"></span></div>
  <div class="notice">[Notification feed-New items in the feeds are highlighted in blueand they stay highlighted until cleared. You can clear highlights once.]</div>
  <div class="notify">Notification
    <svg width="16" height="14" viewBox="0 0 16 14"><path d="M0 0h16v10H8l-4 4v-4H0z" fill="#3a9fc4"/></svg>
  </div>
</header>

<nav class="nav">
  <a class="browse" href="#">BROWSE &nbsp;▾</a>
  <a href="#" style="left:196px;width:78px">PROJECTS</a>
  <span class="sep" style="left:292px"></span>
  <a href="#" style="left:320px;width:95px">HOW IT WORKS</a>
  <span class="sep" style="left:444px"></span>
  <a href="#" style="left:464px;width:60px">PLAN</a>
  <span class="sep" style="left:545px"></span>
  <a href="#" style="left:570px;width:90px">MY ACCOUNT</a>
  <span class="sep" style="left:684px"></span>
  <a href="#" style="left:720px;width:20px"><svg width="9" height="9" viewBox="0 0 10 10"><circle cx="4" cy="4" r="3" fill="none" stroke="#fff" stroke-width="1.6"/><path d="M6.2 6.2 9 9" stroke="#fff" stroke-width="1.8"/></svg></a>
</nav>

<section class="hero" role="img" aria-label="Photo of a smiling businessman in a suit holding a laptop in a bright office">
  <span class="arrow" style="left:16px"></span>
  <span class="arrow" style="left:764px"></span>
  <h1>CONVERT MORE<span>CUSTOMERS</span></h1>
  <p>Experience the power of experts collaborating on your project.</p>
  <div class="cta">GET STARTED</div>
</section>

<aside class="panel filters">
  <div class="panel-head"><h2>FILTERS</h2>
    <svg width="11" height="9" viewBox="0 0 11 9"><path d="M0 1h11M0 3.5h11M0 6h11M0 8.5h11" stroke="#3a9fc4" stroke-width="1.2"/></svg>
  </div>
  <div class="price">
    <h3>Price</h3>
    <ul>
      <li>Under <span class="tick"></span>1,000 (58,01,601)</li>
      <li><span class="tick"></span>1,000 - <span class="tick"></span>5,000 (4,86,238)</li>
      <li><span class="tick"></span>5,000 - <span class="tick"></span>10,000 (18,414)</li>
      <li><span class="tick"></span>10,000 - <span class="tick"></span>20,000 (4,168)</li>
      <li>Over <span class="tick"></span>20,000 (2,091)</li>
    </ul>
  </div>
  <div class="filter"><svg viewBox="0 0 10 10"><rect x="0.5" y="1" width="9" height="6" fill="none" stroke="#f0901e"/><path d="M3 9h4" stroke="#f0901e"/></svg>Country</div>
  <div class="filter"><svg viewBox="0 0 10 10"><path d="M1 3l4 4 4-4" fill="none" stroke="#f0901e" stroke-width="1.6"/></svg>Categories</div>
  <div class="filter"><svg viewBox="0 0 10 10"><circle cx="5" cy="5" r="4" fill="none" stroke="#f0901e" stroke-width="1.2"/><path d="M5 2.5V5h2" stroke="#f0901e"/></svg>Time Left</div>
  <div class="filter"><svg viewBox="0 0 10 10"><path d="M1 9 9 1M2 3h3M5 7h3" stroke="#f0901e" stroke-width="1.2"/></svg>Active | Expired</div>
  <div class="filter"><svg viewBox="0 0 10 10"><circle cx="3.5" cy="6" r="2.5" fill="#f0901e"/><circle cx="7.5" cy="3" r="2" fill="#f0901e"/></svg>Contains adult content</div>
  <div class="filter"><svg viewBox="0 0 10 10"><circle cx="3" cy="3" r="2.2" fill="none" stroke="#f0901e" stroke-width="1.3"/><path d="M4.5 4.5 9 9M7 7l1.5-1.5" stroke="#f0901e" stroke-width="1.3"/></svg>keywords</div>
  <div class="filter"><svg viewBox="0 0 10 10"><rect x="1.5" y="2" width="7" height="5" fill="none" stroke="#f0901e"/><path d="M0 8.5h10" stroke="#f0901e"/></svg>followers</div>
  <div class="filter" style="padding-left:33px">[etc.]</div>
</aside>

<section class="panel projects">
  <div class="panel-head"><h2>Crowd Projects:</h2><span class="sort">Sort: Price &nbsp;/&nbsp; country &nbsp;/&nbsp; Time left</span></div>
  <div class="item" style="height:61px">Morbi in ante arcu. Maecenas sit amet sem vel But I must explain to you how all this mistaken idea of denouncing pleasure and praising pain was born and I will give you a complete account of the system, and expound the<div class="meta">.$80, U.K., time left: 6 days</div></div>
  <div class="item" style="height:64px">At vero eos et accusamus et iusto odio dignissimos ducimus qui blanditiis praesentium voluptatum deleniti atque corrupti quos dolores et quas molestias excepturi sint<div class="meta">$90, CA., time left: 6 days Featured</div></div>
  <div class="item" style="height:65px">Sed ut perspiciatis unde omnis iste natus error sit voluptatem accusantium doloremque laudantium, totam rem aperiam, eaque ipsa quae ab illo inventore veritatis<div class="meta">$250, U.S., time left: 6 days</div></div>
  <div class="item" style="height:64px">On the other hand, we denounce with righteous indignation and dislike men who are so beguiled and demoralized by &nbsp;the charms of pleasure of the moment, so blinded<div class="meta">$62, U.K., time left: 6 days</div></div>
  <div class="item" style="height:64px">Morbi in ante arcu. Maecenas sit amet sem vel But I must explain to you how all this mistaken idea of denouncing pleasure and praising pain was born and I will give you a complete account of the system, and expound the<div class="meta">$48, U.S., time left: 6 days</div></div>
  <div class="item" style="height:52px;border-bottom:0">Morbi in ante arcu. Maecenas sit amet sem vel<div class="meta">.$80, U.K., time left: 6 days</div>
    <svg class="check" width="10" height="10" viewBox="0 0 10 10"><circle cx="5" cy="5" r="4.3" fill="none" stroke="#999"/><path d="M3 5l1.5 1.5L7 3.5" fill="none" stroke="#999"/></svg>
  </div>
</section>

<section class="testimonials">
  <h2>TESTIMONIALS</h2>
  <p class="lead">At vero eos et accusamus et iusto odio dignissimos ducimus qui blanditiis praesentium voluptatum deleniti atque corrupti quos dolores et quas molestias excepturi sint occaecati cupiditate non provident,</p>
</section>
<div class="divider"></div>
<span class="chev" style="left:102px">‹</span>
<div class="avatar" style="left:133px;background:radial-gradient(circle at 50% 45%,#d9b49a,#8a6a55)" role="img" aria-label="Portrait photo of a smiling woman"></div>
<div class="quote" style="left:226px"><h4>DANE HOLLOWAY,</h4><div class="date">Posted on 24 Nov 2015</div>"With Pelmora I have multiple experts perfecting my content and I only pay for the feedback I find valuable. It's perfect"</div>
<div class="avatar" style="left:419px;background:radial-gradient(circle at 50% 40%,#c9a88f,#3a3d44)" role="img" aria-label="Portrait photo of a man in a suit and red tie"></div>
<div class="quote" style="left:511px"><h4>MARC ELLERY,</h4><div class="date">Posted on 24 Nov 2015</div>"Before you put any content in front of your audience, crowdsource it with Pelmora, you won't regret it"</div>
<span class="chev" style="left:691px">›</span>

<footer class="footer">
  <nav>HOME<span>/</span>PROJECTS<span>/</span>HOW IT WORKS<span>/</span>MY ACCOUNT</nav>
  <small>2015 © Copy right .pelmora .all right reserved</small>
  <div class="social"><i></i><i></i><i></i><i></i></div>
</footer>
</body>
</html>
```